Powerpoint template and intro presentation

I have a short presentation of 6 slides that I'd like to be made pretty, see attached below - called target companies Intro.

I'd also like a template incorporating my logo which I have attached below as well

I've attached a jpeg with the logo with white background that is the logo that I would like to incorporate.

Powerpoint and logo file has been uploaded

```html
<!DOCTYPE html>
<html lang="en">
<head>
<meta charset="utf-8">
<title>Stratus Harbour Services – Slide 2</title>
<link rel="stylesheet" href="https://fonts.googleapis.com/css2?family=Questrial&display=swap">
<style>
  :root {
    --page-bg: #eeeae3;
    --slide-bg: #ffffff;
    --brand-green: #7cbb2c;
    --rule-green: #cde6ae;
    --rule-grey: #c9c9cc;
    --text-grey: #4a4a4f;
    --photo-tone: #d9d9d9;
  }
  html, body {
    margin: 0;
    width: 1200px;
    height: 1000px;
    overflow: hidden;
    background: var(--page-bg);
  }
  .slide {
    position: absolute;
    left: 33px;
    top: 70px;
    width: 1135px;
    height: 850px;
    background: var(--slide-bg);
    box-shadow: 0 2px 6px rgba(0,0,0,0.18);
    font-family: "Questrial", "Century Gothic", sans-serif;
    color: var(--text-grey);
    overflow: hidden;
  }
  .handshake-photo {
    position: absolute;
    left: 540px;
    top: 440px;
    width: 595px;
    height: 330px;
    background: linear-gradient(90deg, rgba(217,217,217,0) 0%, rgba(210,210,210,0.55) 45%, rgba(225,225,225,0.35) 100%);
    border-radius: 40px 0 0 40px;
  }
  .brand-mark {
    position: absolute;
    left: 57px;
    top: 52px;
    display: flex;
    align-items: center;
    gap: 8px;
    color: var(--brand-green);
    font-size: 15px;
    line-height: 1.15;
    letter-spacing: 1px;
    text-transform: uppercase;
  }
  .brand-mark .dot {
    width: 22px;
    height: 22px;
    border-radius: 50%;
    background: var(--brand-green);
    flex: none;
  }
  .slide-title {
    position: absolute;
    left: 229px;
    top: 66px;
    margin: 0;
    font-weight: 400;
    font-size: 41px;
    letter-spacing: 1px;
    color: var(--brand-green);
  }
  .header-rule, .footer-rule {
    position: absolute;
    height: 6px;
    background: var(--rule-green);
    border-bottom: 2px solid var(--rule-grey);
    box-shadow: 0 3px 0 #fff;
  }
  .header-rule { left: 229px; right: 0; top: 117px; }
  .footer-rule { left: 0; width: 1027px; top: 790px; }
  .points {
    position: absolute;
    left: 67px;
    top: 170px;
    width: 900px;
    margin: 0;
    padding: 0;
    list-style: none;
    font-size: 33px;
    line-height: 35px;
    letter-spacing: 0.6px;
  }
  .points li {
    position: relative;
    padding-left: 45px;
    margin-bottom: 60px;
  }
  .points li:nth-child(3) { margin-bottom: 60px; }
  .points li::before {
    content: "";
    position: absolute;
    left: 4px;
    top: 13px;
    width: 16px;
    height: 16px;
    border-radius: 50%;
    background: var(--brand-green);
  }
  .page-number {
    position: absolute;
    left: 1034px;
    top: 793px;
    width: 50px;
    height: 30px;
    border-radius: 15px;
    background: var(--brand-green);
    color: #fff;
    font-family: "Questrial", sans-serif;
    font-size: 15px;
    line-height: 32px;
    text-align: center;
  }
</style>
</head>
<body>
  <section class="slide">
    <div class="handshake-photo" role="img" aria-label="Greyscale photo of two hands in a business handshake"></div>

    <div class="brand-mark">
      <span class="dot"></span>
      <span>Stratus<br>Harbour</span>
    </div>

    <h1 class="slide-title">Stratus Harbour Services</h1>
    <div class="header-rule"></div>

    <ul class="points">
      <li>Working with private equity funds to find Australian based cloud companies to invest in.</li>
      <li>Looking to partner with thought leaders and innovators to create a competitive cloud offering.</li>
      <li>Want to work with existing management to grow the business.</li>
      <li>We believe that market is ready for consolidation.</li>
      <li>We are committed to building a large and successful Australian owned cloud services business.</li>
    </ul>

    <div class="footer-rule"></div>
    <div class="page-number">2</div>
  </section>
</body>
</html>
```